label design peanut butter jar to be marketed internationally for a singapore based company

We need design of 2 labels creamy peanut butter and crunch peanut butter
The design is the same only photo of product
And wording change
The logo nordvel remains the same and has to be used logo of peanut has to be used
Some idea designs by our in house designer
Enclosed .
Plus a design of a competitor lunar meadow

Target Market(s)

international specially emerging markets

Industry/Entity Type

It Company

Requirements
Must have
• nordvel logo
• peanut logo

```html
<!DOCTYPE html>
<html lang="en">
<head>
<meta charset="utf-8">
<title>Nordvel Creamy Peanut Butter Label</title>
<link rel="stylesheet" href="https://fonts.googleapis.com/css2?family=Montserrat:wght@600;700&family=Graduate&display=swap">
<style>
  :root {
    --page: #ffffff;
    --purple: #5f3a8c;
    --purple-deep: #4e2c78;
    --orange: #f0741f;
    --orange-light: #f7a21e;
    --sun: #fde047;
    --cream: #ffffff;
    --butter-light: #d9a468;
    --butter-dark: #b7783c;
  }
  * { box-sizing: border-box; margin: 0; padding: 0; }
  html, body {
    width: 871px;
    height: 1200px;
    overflow: hidden;
    background: var(--page);
  }
  .label {
    position: absolute;
    left: 86px;
    top: 180px;
    width: 700px;
    height: 800px;
  }
  .label-art {
    position: absolute;
    inset: 0;
  }
  .brand {
    position: absolute;
    left: 0;
    top: 132px;
    width: 700px;
    text-align: center;
    font-family: "Montserrat", sans-serif;
    font-weight: 700;
    font-size: 66px;
    letter-spacing: 9px;
    color: var(--purple);
    line-height: 1;
  }
  .product-photo {
    position: absolute;
    left: 70px;
    top: 262px;
    width: 400px;
    height: 300px;
    border-radius: 48% 52% 40% 60% / 55% 45% 55% 45%;
    background: radial-gradient(ellipse at 55% 40%, var(--butter-light), var(--butter-dark));
  }
  .flavour {
    position: absolute;
    left: 0;
    top: 618px;
    width: 700px;
    text-align: center;
    font-family: "Graduate", serif;
    color: var(--purple);
    line-height: 1;
  }
  .flavour-top { font-size: 38px; display: block; }
  .flavour-bottom { font-size: 30px; display: block; margin-top: 4px; }
  .net-weight {
    position: absolute;
    left: 0;
    top: 754px;
    width: 700px;
    text-align: center;
    font-family: "Montserrat", sans-serif;
    font-weight: 700;
    font-size: 17px;
    letter-spacing: 1px;
    color: var(--cream);
  }
</style>
</head>
<body>
  <main class="label">
    <svg class="label-art" width="700" height="800" viewBox="0 0 700 800" aria-hidden="true">
      <defs>
        <radialGradient id="sunburst" cx="50%" cy="50%" r="60%">
          <stop offset="0" stop-color="var(--sun)"/>
          <stop offset="0.45" stop-color="var(--orange-light)"/>
          <stop offset="1" stop-color="var(--orange)"/>
        </radialGradient>
      </defs>
      <rect class="band" x="0" y="0" width="700" height="800" fill="var(--purple)"/>
      <path class="sun-panel" d="M0 60 Q350 10 700 60 L700 690 Q350 730 0 690 Z" fill="url(#sunburst)"/>
      <path class="sun-frame" d="M60 110 Q350 40 640 110 Q700 380 640 660 Q350 720 60 660 Q0 380 60 110 Z" fill="none" stroke="var(--purple-deep)" stroke-width="26"/>
      <path class="sun-line" d="M0 62 Q350 12 700 62" fill="none" stroke="var(--sun)" stroke-width="5"/>
      <path class="sun-line" d="M0 688 Q350 728 700 688" fill="none" stroke="var(--sun)" stroke-width="5"/>
      <ellipse class="brand-oval" cx="350" cy="165" rx="235" ry="82" fill="var(--cream)" stroke="var(--orange)" stroke-width="8"/>
      <ellipse class="flavour-oval" cx="350" cy="655" rx="178" ry="60" fill="var(--cream)" stroke="var(--orange)" stroke-width="7"/>
    </svg>
    <div class="brand">NORDVEL</div>
    <div class="product-photo" role="img" aria-label="Spoon heaped with swirled creamy peanut butter"></div>
    <div class="flavour">
      <span class="flavour-top">CREAMY</span>
      <span class="flavour-bottom">PEANUT BUTTER</span>
    </div>
    <div class="net-weight">200 GRAMS</div>
  </main>
</body>
</html>
```